spoonful of caviar

I am looking to design a flyer/leaflet to distribute to houses or post on shop windows that invite people to buy caviar. The moto is: With our LOW prices you can now afford real CAVIAR by the SPOONFUL!
Customers will be offered three-four type of product or more on the website. There will be price advertised on the leaflet, brief description of the product and delivery terms: Free local delivery* (Wed & Fri, For more options: call 07480392615. The actual products are on the attached files and the theme ideas are there too.
Shop

```html
<!DOCTYPE html>
<html lang="en">
<head>
<meta charset="utf-8">
<title>Roefield Caviar Flyer</title>
<link rel="stylesheet" href="https://fonts.googleapis.com/css2?family=Anton&family=Questrial&family=Open+Sans:wght@700;800&display=swap">
<style>
  :root {
    --page-bg: #e4e4e4;
    --front-top: #a9c3c4;
    --front-bottom: #4f6f78;
    --sage: #6f8a68;
    --note-green: #3f7a2c;
    --white: #ffffff;
    --ink: #1c1c1c;
    --pill: #2f4a55;
    --band-grey: #8b8f88;
    --caviar: #e0782a;
    --caviar-deep: #8a3512;
  }
  html, body {
    margin: 0; padding: 0;
    width: 1200px; height: 1000px;
    overflow: hidden;
    background: var(--page-bg);
  }
  .canvas { position: relative; width: 1200px; height: 1000px; }

  .flyer {
    position: absolute; left: 100px; width: 1000px;
    overflow: hidden; box-shadow: 0 6px 18px rgba(0,0,0,.18);
  }

  /* Front */
  .flyer-front {
    top: 30px; height: 450px;
    background: radial-gradient(ellipse at 40% 45%, var(--front-top) 0%, #7d9ea3 45%, var(--front-bottom) 100%);
  }
  .spoon-photo { position: absolute; left: 240px; top: 40px; width: 460px; height: 320px; }
  .headline {
    position: absolute; right: 30px; top: 30px; width: 420px; margin: 0;
    font-family: "Anton", Impact, sans-serif; text-align: center;
    color: var(--white); line-height: 1.05; text-transform: uppercase; font-weight: 400;
  }
  .headline .line {
    display: block; font-size: 40px;
    text-shadow: 2px 2px 0 var(--ink), -1px -1px 0 var(--ink), 1px -1px 0 var(--ink), -1px 1px 0 var(--ink);
  }
  .headline .line-brand { font-size: 62px; color: var(--white); text-shadow: none; margin-top: 4px; }
  .contact-pill {
    position: absolute; left: 24px; top: 362px;
    display: flex; align-items: center; gap: 10px;
    background: var(--pill); color: var(--white);
    border-radius: 30px; padding: 8px 22px 8px 12px;
    font-family: "Questrial", sans-serif;
  }
  .contact-pill .label { position: absolute; left: 60px; top: -26px; font-size: 17px; white-space: nowrap; }
  .contact-pill .number { font-family: "Open Sans", sans-serif; font-weight: 800; font-size: 30px; letter-spacing: 1px; }
  .shelf-life {
    position: absolute; left: 420px; top: 380px; margin: 0;
    font-family: "Questrial", sans-serif; font-size: 11px; color: var(--white);
  }
  .product-tins { position: absolute; right: 40px; bottom: 18px; width: 230px; height: 130px; }

  /* Back */
  .flyer-back { top: 510px; height: 460px; background: var(--sage); }
  .about-copy {
    position: absolute; left: 34px; top: 20px; width: 660px;
    font-family: "Questrial", sans-serif; font-size: 12.5px; line-height: 1.4;
    color: var(--white);
  }
  .about-copy p { margin: 0 0 6px; }
  .note-band {
    position: absolute; left: 0; top: 168px; width: 720px; margin: 0;
    background: var(--white); border-radius: 0 28px 28px 0;
    padding: 10px 24px 10px 34px; box-sizing: border-box;
    font-family: "Open Sans", sans-serif; font-weight: 800; font-size: 16px; line-height: 1.3;
    color: var(--note-green);
  }
  .shipping {
    position: absolute; left: 34px; top: 240px; width: 440px;
    font-family: "Questrial", sans-serif; color: var(--white);
  }
  .shipping h2 {
    margin: 0 0 6px; font-family: "Open Sans", sans-serif; font-weight: 800;
    font-size: 22px; letter-spacing: .5px;
  }
  .shipping p { margin: 0; font-size: 12.5px; line-height: 1.4; }
  .info-band { position: absolute; left: 0; top: 370px; width: 1000px; height: 90px; background: var(--white); }
  .info-label {
    position: absolute; left: 40px; top: 388px; margin: 0;
    font-family: "Questrial", sans-serif; font-size: 34px; letter-spacing: 9px;
    color: var(--band-grey);
  }
  .back-number {
    position: absolute; right: 40px; top: 384px;
    display: flex; align-items: center; gap: 12px;
    font-family: "Open Sans", sans-serif; font-weight: 800; font-size: 46px; letter-spacing: 3px;
    color: var(--white); -webkit-text-stroke: 2px var(--band-grey);
  }
  .serving-large { position: absolute; left: 760px; top: 170px; width: 190px; height: 190px; }
  .serving-small { position: absolute; left: 880px; top: 40px; width: 100px; height: 100px; }
  .back-tins { position: absolute; left: 520px; top: 240px; width: 220px; height: 125px; }
</style>
</head>
<body>
<main class="canvas">

  <section class="flyer flyer-front">
    <svg class="spoon-photo" viewBox="0 0 460 320" role="img" aria-label="Photo of a silver spoon heaped with glossy red caviar">
      <defs>
        <radialGradient id="caviarGlow" cx="50%" cy="45%" r="60%">
          <stop offset="0%" stop-color="#f7a24a"/>
          <stop offset="55%" stop-color="#e0782a"/>
          <stop offset="100%" stop-color="#8a3512"/>
        </radialGradient>
      </defs>
      <ellipse cx="230" cy="170" rx="200" ry="120" fill="url(#caviarGlow)"/>
    </svg>

    <h1 class="headline">
      <span class="line">With our low prices</span>
      <span class="line">you can now afford</span>
      <span class="line">real caviar by</span>
      <span class="line line-brand">Roefield</span>
    </h1>

    <p class="shelf-life">Shelf life 6 months at temperature 0° to -6°C</p>

    <div class="contact-pill">
      <span class="label">For more information</span>
      <svg width="32" height="32" viewBox="0 0 24 24" aria-hidden="true">
        <circle cx="12" cy="12" r="12" fill="#ffffff"/>
        <path d="M8 6c1 0 1.6 2 1.6 2.6S8.6 10 8.8 10.6c.5 1.4 2.1 3 3.5 3.5.6.2 1.4-.8 2-.8s2.6.6 2.6 1.6-1.2 2.1-2.4 2.1C10.3 17 7 13.7 7 9.4 7 8.2 7 6 8 6z" fill="#2f4a55"/>
      </svg>
      <span class="number">07480392615</span>
    </div>

    <svg class="product-tins" viewBox="0 0 230 130" role="img" aria-label="Photo of two caviar tins, one open showing red roe">
      <ellipse cx="80" cy="75" rx="75" ry="50" fill="#d8352a"/>
      <ellipse cx="170" cy="60" rx="55" ry="55" fill="#2a2a2a"/>
    </svg>
  </section>

  <section class="flyer flyer-back">
    <div class="about-copy">
      <p>A MUST HAVE for Russian culture lovers!!! It would make a delicious addition to your party or an amazing and unique gift for any occasion. Too good to miss!!!</p>
      <p>Look out for Amber Pearl Caviar. Of greatest value and quality, it has a fresh taste and distinctly bigger, gorgeous, succulent red grain. This delicacy is rich in Omega-3 polyunsaturated fats, proteins and vitamins.</p>
      <p>Russian caviar has long been a delicacy for thousands of people. Our purchasing power allows us to bring it to you at a price that will make you, your family and your friends smile. Keep a pot in the fridge as a reminder of delicious times.</p>
    </div>

    <p class="note-band">PLEAS NOTE: Actual Caviar colour and size might vary slightly from the photos provided as each harvest naturally differs.</p>

    <div class="shipping">
      <h2>PAYMENTS, HANDLING &amp; SHIPPING</h2>
      <p>If you pay by card we will do our best to send your goods the next day, or on Monday if it is the weekend. All items shipped within England are traceable and insured. Please don't be put off by the fact that items are sent from England; your order is trackable.</p>
    </div>

    <svg class="back-tins" viewBox="0 0 220 125" role="img" aria-label="Photo of two caviar tins, one open showing red roe">
      <ellipse cx="75" cy="72" rx="70" ry="48" fill="#d8352a"/>
      <ellipse cx="165" cy="58" rx="52" ry="52" fill="#2a2a2a"/>
    </svg>
    <svg class="serving-large" viewBox="0 0 190 190" role="img" aria-label="Round photo of a plated dish garnished with red caviar">
      <circle cx="95" cy="95" r="93" fill="#b9b3a8"/>
    </svg>
    <svg class="serving-small" viewBox="0 0 100 100" role="img" aria-label="Round photo of a caviar canape">
      <circle cx="50" cy="50" r="48" fill="#a89885"/>
    </svg>

    <div class="info-band" aria-hidden="true"></div>
    <p class="info-label">For more information</p>
    <div class="back-number">
      <svg width="36" height="36" viewBox="0 0 24 24" aria-hidden="true">
        <path d="M7 3c1.4 0 2.2 2.8 2.2 3.6S7.8 8.5 8.1 9.3c.7 2 2.9 4.2 4.9 4.9.8.3 2-1.1 2.8-1.1s3.6.8 3.6 2.2-1.7 2.9-3.3 2.9C10 18.2 5.8 14 5.8 8 5.8 6.3 5.6 3 7 3z" fill="#8b8f88"/>
      </svg>
      <span>07480392615</span>
    </div>
  </section>

</main>
</body>
</html>
```